Create Website for new company called "Verdale Lodge 37"

Verdale Lodge 37 is a new business situated in Southwestern Colorado. We are creating a business that will rent out spaces where clients can grow their own marijuana. Picture a large green house with partitioned spaces that are secured by a lock. Best way to envision this would be to think of a storage business that rents out storage rooms. The difference is that we will be having the units inside a green house ( for growing purposes) Picture a small area that is secured by locks, Picture an area that has the ability to provide state of the art security, cameras etc. We want to focus our efforts on professionals, blue collar workers and end users of marijuana. Our emphasis is in the area of assisting those whom wish to grow their own plants. We want to provide them a safe facility in which to do that. . Keep in mind that we also build custom grow rooms at clients homes and provide a grow pod (lease these) where a small grow unit will be delivered and picked up from our clients whom want to lease a unit for a short amount of time. We have a business card ( just designed) and will send that information to those whom express an interests in this project. We want to be able to sign people up for our services by entering an agreement and signing the agreement while on the internet. We want to provide our services to those whom consume recreational and medical marijuana. This site will need to gather information I.e email addresses so that we can followup with offers. This is a tremendous opportunity for the right designer. We will be creating many more websites as other states come on line and make marijuana legal to consume. Use the business card model for a point of reference of how we envision the concept. That is a business card we just recently printed. The hands and the plant is our logo so far. Open to suggestions. There will be three levels of service. Bronze, Silver, Gold or Platinum. We will also have a retail biz down the road but not at the present time.

Target Market(s)

Ages 21-60

Industry/Entity Type

Medical

Logo Text

Verdale Lodge 37.

Number of Pages Required

5+ page

Requirements
Must have
• Clean appearance not to busy , easily navigable from link to link, page to page. Must have ability down the road to enter into a contractual agreement via the website. Must use our provided logo and example of that is on our business card that will be uploaded here shortly. We would like to have the colors that are on the business card however if you have suggestions or color schemes that you want us to consider that is okay.
Nice to have
• Nice to have a animation of seed to weed and how clients can save a tremendous amount of money growing their own cannabis. Nice to have testimonial page or feedback page. Have a membership component to website,
Should not have
• No flashing lights, etc. Not to busy in terms of animations.

```html
<!DOCTYPE html>
<html lang="en">
<head>
<meta charset="utf-8">
<title>Verdale Lodge 37</title>
<link href="https://fonts.googleapis.com/css2?family=Oswald:wght@300;400&family=Lato:ital,wght@0,400;0,700;1,400&display=swap" rel="stylesheet">
<style>
:root{
  --green:#0f8a3c;
  --green-dark:#0a6d2d;
  --green-light:#1a9b48;
  --ink:#333;
  --grey-text:#777;
  --panel:#f4f4f4;
  --footer:#333;
  --footer-panel:#464646;
  --white:#fff;
  --accent:#c9782c;
}
*{margin:0;padding:0;box-sizing:border-box}
html,body{width:780px;height:1200px;overflow:hidden;background:#fff}
body{font-family:'Lato',sans-serif;color:var(--ink)}
.page{position:relative;width:780px;height:1200px;overflow:hidden}
.abs{position:absolute}
.head-font{font-family:'Oswald',sans-serif;font-weight:400}

/* top bar */
.topbar{left:0;top:0;width:780px;height:52px;background:linear-gradient(#17a04b,var(--green-dark))}
.phone{left:86px;top:17px;color:var(--white);font-size:16px;display:flex;align-items:center;gap:6px}
.social{top:15px;display:flex;gap:6px}
.social span{width:22px;height:22px;border-radius:50%;background:var(--white);display:block}

/* navigation */
.nav{left:0;top:52px;width:780px;height:36px;background:var(--white);box-shadow:0 1px 2px rgba(0,0,0,.2)}
.nav-item{top:6px;height:24px;line-height:24px;font-size:9.5px;font-weight:700;text-transform:uppercase;color:#222;padding:0 10px;border-right:1px solid #bbb}
.nav-item.active{background:var(--green);color:var(--white);border:none;padding:0 14px}
.nav-item.last{border-right:1px solid var(--accent)}

.brand{left:293px;top:16px;width:198px;height:110px;border-radius:50%;background:var(--white);border:5px solid #d4ead9;box-shadow:0 0 0 2px var(--green-light);display:flex;align-items:center;justify-content:center;gap:6px;font-family:'Oswald',sans-serif;font-size:21px;color:#3b3b3b}
.brand i{width:10px;height:10px;background:var(--green);border-radius:50%;display:block}

/* hero */
.hero{left:0;top:88px;width:780px;height:310px;background:radial-gradient(ellipse at 70% 60%,#c99a84 0,#8a7a5c 14%,transparent 28%),linear-gradient(120deg,#2f6e27,#5d9a3f 40%,#3f7a2c 70%,#6da24b)}
.caption{left:86px;top:153px;width:277px;height:66px;background:rgba(20,40,20,.55);color:var(--white);font-family:'Oswald',sans-serif;font-weight:300;font-size:20px;line-height:28px;padding:4px 11px}
.arrow{top:229px;width:29px;height:29px;border-radius:50%;border:2px solid rgba(255,255,255,.8);background:rgba(0,0,0,.25)}

/* services */
.services{left:0;top:398px;width:780px;height:209px;background:var(--panel)}
.card{top:364px;width:187px;height:213px;background:var(--white);border:1px solid #bbb;border-radius:4px;box-shadow:0 8px 6px -6px rgba(0,0,0,.35)}
.card-title{height:36px;background:linear-gradient(var(--green-light),var(--green-dark));border-radius:4px 4px 0 0;color:var(--white);font-family:'Oswald',sans-serif;font-size:15px;line-height:36px;padding-left:13px}
.card-media{margin:10px 0 0 10px;width:168px;height:73px;border:3px solid #666}
.card-text{margin:8px 10px 0;font-size:9.2px;line-height:14.6px;color:var(--grey-text)}
.read-more{font-size:8px;font-weight:700;color:#333;text-decoration:underline;text-transform:uppercase}
.card .read-more{display:block;margin:6px 10px 0}

/* welcome */
.welcome{left:0;top:607px;width:780px;height:183px;background:linear-gradient(var(--green-light),var(--green-dark))}
.video{left:86px;top:626px;width:187px;height:145px;background:linear-gradient(160deg,#6a8f4a,#3c6a2c 60%,#2c4f22)}
.play{left:166px;top:680px;width:24px;height:24px;border-radius:50%;background:rgba(255,255,255,.85)}
.vbar{left:86px;top:752px;width:187px;height:19px;background:#1a1a1a;color:var(--white);font-size:7px;display:flex;align-items:center;gap:6px;padding:0 8px}
.vbar .track{flex:1;height:4px;background:#666;border-radius:2px}
.welcome-title{left:297px;top:622px;color:var(--white);font-size:18px}
.welcome-rule{left:297px;top:651px;width:397px;border-top:1px solid rgba(255,255,255,.35)}
.welcome-text{left:297px;top:662px;width:400px;color:var(--white);font-size:9.4px;line-height:14.8px}
.welcome-text p+p{margin-top:14px}
.welcome-more{left:297px;top:755px;color:var(--white)}

/* testimonial + news */
.info{left:0;top:790px;width:780px;height:225px;background:linear-gradient(#f8f8f8,#e9e9e9)}
.section-title{top:810px;font-size:15px;color:#333;display:flex;align-items:center;gap:8px}
.section-rule{top:837px;border-top:1px solid #999}
.quote{left:86px;top:854px;width:279px;height:107px;background:#6b6b6b;border-radius:3px;color:var(--white);font-style:italic;font-size:9.2px;line-height:14.8px;padding:13px 14px 0 18px}
.quote-tail{left:110px;top:960px}
.quote-name{left:141px;top:968px;font-size:10px;font-weight:700;color:#333}
.divider{left:389px;top:838px;width:2px;height:140px;background:linear-gradient(rgba(0,0,0,0),rgba(0,0,0,.18),rgba(0,0,0,0))}
.news{left:414px;width:280px}
.news-date{font-size:9px;font-weight:700;color:#333;display:flex;align-items:center;gap:5px}
.news-head{font-size:10px;font-weight:700;color:#444;margin:5px 0 0 12px}
.news-body{font-size:9px;line-height:13.5px;color:var(--grey-text);margin:2px 0 0 12px}
.news-sep{left:414px;top:916px;width:280px;border-top:1px dotted #777}

/* footer */
.footer{left:0;top:1015px;width:780px;height:185px;background:var(--footer)}
.quote-panel{left:86px;top:1018px;width:187px;height:182px;background:var(--footer-panel)}
.fh{color:var(--white);font-size:15px}
.field{left:97px;width:165px;height:22px;background:#555;border:1px solid #6a6a6a;color:#aaa;font-size:7px;padding:6px 7px}
.btn{background:var(--green);color:var(--white);font-size:11px;text-align:center}
.news-input{left:296px;top:1052px;width:184px;height:24px;background:#666;color:#ddd;font-size:7.5px;padding:8px}
.footer-line{border-top:1px solid #555}
.foot-text{color:#eee;font-size:9px;line-height:13.5px}
.foot-social{left:590px;top:1053px;display:flex;gap:6px}
.foot-social span{width:22px;height:22px;border-radius:50%;border:2px solid #fff;display:block}
.foot-brand{left:590px;top:1117px;font-family:'Oswald',sans-serif;font-size:17px;color:#bbb;display:flex;align-items:center;gap:5px}
.foot-brand i{width:8px;height:8px;background:var(--accent);display:block}
</style>
</head>
<body>
<div class="page">

  <!-- header -->
  <div class="abs topbar"></div>
  <div class="abs phone">
    <svg width="18" height="18" viewBox="0 0 18 18"><circle cx="9" cy="9" r="8" fill="none" stroke="#fff" stroke-width="1.5"/><path d="M6 5.5l1.5-.5 1 2-1 .8c.5 1.2 1.3 2 2.5 2.5l.8-1 2 1-.5 1.5c-3 .3-6.6-3.2-6.3-6.3z" fill="#fff"/></svg>
    +123-456-7890
  </div>
  <div class="abs social" style="left:590px"><span></span><span></span><span></span><span></span></div>

  <nav class="abs nav">
    <span class="abs nav-item active" style="left:86px">Home</span>
    <span class="abs nav-item" style="left:152px">About Us</span>
    <span class="abs nav-item" style="left:226px;border:none">Services</span>
    <span class="abs nav-item" style="left:496px">Facilities</span>
    <span class="abs nav-item" style="left:556px">Testimonial</span>
    <span class="abs nav-item last" style="left:626px">Contact Us</span>
  </nav>
  <div class="abs brand"><i></i>VERDALE LODGE 37</div>

  <!-- hero -->
  <div class="abs hero" role="img" aria-label="Close-up of a hand touching a cannabis plant among green leaves"></div>
  <h1 class="abs caption">Lorem ipsum dolor sit amet,<br>consectetuer adipiscing elit, sed</h1>
  <div class="abs arrow" style="left:56px"><svg width="25" height="25" viewBox="0 0 25 25"><path d="M14 7l-5 5.5 5 5.5" fill="none" stroke="#fff" stroke-width="1.6"/></svg></div>
  <div class="abs arrow" style="left:695px"><svg width="25" height="25" viewBox="0 0 25 25"><path d="M11 7l5 5.5-5 5.5" fill="none" stroke="#fff" stroke-width="1.6"/></svg></div>

  <!-- services -->
  <div class="abs services"></div>
  <article class="abs card" style="left:86px">
    <h2 class="card-title head-font">FOR LEASE</h2>
    <div class="card-media" style="background:linear-gradient(120deg,#9bb8c4,#c9d6cf 50%,#7fa062)" role="img" aria-label="For lease sign in front of a building"></div>
    <p class="card-text">Lorem ipsum dolor sit ametuer adipiscingi elit, sed diam nmy nibh euismod tincidunt ut laoreet dolore magna am erat visi enim ad minim veniam, quis nostrud exerci</p>
    <a class="read-more">Read More »</a>
  </article>
  <article class="abs card" style="left:297px">
    <h2 class="card-title head-font">FOR LOCK</h2>
    <div class="card-media" style="background:linear-gradient(90deg,#3f5a4a,#8a8a80 50%,#d8d8d2)" role="img" aria-label="Padlock on a wooden door"></div>
    <p class="card-text">Lorem ipsum dolor sit ametuer adipiscingi elit, sed diam nmy nibh euismod tincidunt ut laoreet dolore magna am erat visi enim ad minim veniam, quis nostrud exerci</p>
    <a class="read-more">Read More »</a>
  </article>
  <article class="abs card" style="left:508px">
    <h2 class="card-title head-font">FOR CAMERA</h2>
    <div class="card-media" style="background:linear-gradient(#e0b98c,#b5824f 60%,#8a5a33)" role="img" aria-label="Security camera on a warm background"></div>
    <p class="card-text">Lorem ipsum dolor sit ametuer adipiscingi elit, sed diam nmy nibh euismod tincidunt ut laoreet dolore magna am erat visi enim ad minim veniam, quis nostrud exerci</p>
  </article>

  <!-- welcome -->
  <div class="abs welcome"></div>
  <div class="abs video" role="img" aria-label="Video of an officer inspecting a cannabis grow room"></div>
  <div class="abs play"><svg width="24" height="24" viewBox="0 0 24 24"><path d="M10 7l7 5-7 5z" fill="#222"/></svg></div>
  <div class="abs vbar">
    <svg width="7" height="8" viewBox="0 0 7 8"><path d="M0 0l7 4-7 4z" fill="#fff"/></svg>
    <span>04:59</span><span class="track"></span><span>10:35</span>
    <svg width="9" height="8" viewBox="0 0 9 8"><path d="M0 2.5h2l3-2.5v8l-3-2.5h-2z" fill="#fff"/></svg>
  </div>
  <h2 class="abs welcome-title head-font">Welcome To Verdale Lodge 37</h2>
  <div class="abs welcome-rule"></div>
  <div class="abs welcome-text">
    <p>Lorem ipsum dolor sit amet, consectetuer adipiscing elit, sed diam nonummy nibh euismod ut laoreet dolore magna aliquam erat volutpat. Ut wisi enim ad minim veniam, quis nostrud etation ullamcorper suscipit lobortis nisl ut aliquip ex ea commodo consequat.</p>
    <p>Duis autem vel eum iriure dor in hendrerit in vulputate velit esse molestie &nbsp;vel illum dolore eu feugiat nulla facilisro eros et accumsan et iusto odio dignissim qui blandit praesent luptatum zzril.</p>
  </div>
  <a class="abs read-more welcome-more">Read More »</a>

  <!-- testimonial & news -->
  <div class="abs info"></div>
  <h2 class="abs section-title head-font" style="left:86px">
    <svg width="20" height="17" viewBox="0 0 20 17"><path d="M1 1h11v7h-6l-3 3v-3h-2z" fill="var(--green)"/><path d="M14 5h5v7h-2v3l-3-3h-5v-2h5z" fill="var(--green)"/></svg>
    Client Testimonial
  </h2>
  <div class="abs section-rule" style="left:86px;width:281px"></div>
  <div class="abs quote">Lorem ipsum dolor sit amet, consectetuer adipi sed diam nony nibh euismod ut laoreet dolore magna aliquam erat volut wisi enim ad minim veniam, quis nostrud etation ullamcorpecipit lobortis nisl ut aliquip ex ea commodo consequatuis autem vel eum iriure dor in hendrerit in vulputate velit esse molestie &nbsp;vel illum dolore</div>
  <svg class="abs quote-tail" width="24" height="14" viewBox="0 0 24 14"><path d="M0 0h24l-2 14z" fill="#6b6b6b"/></svg>
  <p class="abs quote-name">Mr. Nisl Ut Aliquip</p>
  <div class="abs divider"></div>

  <h2 class="abs section-title head-font" style="left:414px">
    <svg width="22" height="17" viewBox="0 0 22 17"><path d="M1 6h4l9-5v14l-9-5h-1z" fill="var(--green)"/><path d="M4 10l2 6h2l-1-6z" fill="var(--green)"/></svg>
    Latest News
  </h2>
  <div class="abs section-rule" style="left:414px;width:281px"></div>
  <div class="abs news" style="top:853px">
    <p class="news-date"><svg width="8" height="8"><rect width="8" height="8" fill="#999"/></svg>14-March-2014</p>
    <p class="news-head">Exerci tation ullamcorper suscipit lobortis nisl ut aliquip.</p>
    <p class="news-body">Lorem ipsum dolor sit amet, consectetuer adipiscing eli sed di nonmmy nibh euismod tincidunt ut laoreet dolore ma aliquam erat volutpat.</p>
  </div>
  <div class="abs news-sep"></div>
  <div class="abs news" style="top:929px">
    <p class="news-date"><svg width="8" height="8"><rect width="8" height="8" fill="#999"/></svg>14-March-2014</p>
    <p class="news-head">Mullamcorper suscipit lobortis nisl ut aliquip.</p>
    <p class="news-body">nibh euismod tincidunt ut laoreet dolore ma aliquam erat volutpat.</p>
  </div>

  <!-- footer -->
  <footer>
    <div class="abs footer"></div>
    <div class="abs quote-panel"></div>
    <h3 class="abs fh head-font" style="left:98px;top:1026px;display:flex;gap:8px;align-items:center">
      <svg width="19" height="16" viewBox="0 0 19 16"><path d="M1 6l8.5-5 8.5 5v9h-17z" fill="none" stroke="#fff" stroke-width="1.5"/><path d="M1 6l8.5 5 8.5-5" fill="none" stroke="#fff" stroke-width="1.5"/></svg>
      Request a Quote
    </h3>
    <div class="abs field" style="top:1056px">Name</div>
    <div class="abs field" style="top:1082px">Email</div>
    <div class="abs field" style="top:1110px;height:44px">Message</div>
    <div class="abs btn" style="left:97px;top:1163px;width:49px;height:24px;line-height:24px">SEND</div>

    <h3 class="abs fh head-font" style="left:296px;top:1025px;font-size:13px">News Latter Signup</h3>
    <div class="abs news-input">Enter Your Email</div>
    <div class="abs btn" style="left:486px;top:1052px;width:55px;height:24px;line-height:24px">SUBMIT</div>
    <div class="abs" style="left:563px;top:1037px;height:44px;border-left:1px solid #555"></div>

    <h3 class="abs fh head-font" style="left:589px;top:1025px;font-size:13px">Socail Connect</h3>
    <div class="abs foot-social"><span></span><span></span><span></span><span></span></div>

    <div class="abs footer-line" style="left:296px;top:1093px;width:398px"></div>
    <svg class="abs" style="left:297px;top:1108px" width="9" height="13" viewBox="0 0 9 13"><path d="M4.5 0a4.5 4.5 0 0 0-4.5 4.5c0 3 4.5 8.5 4.5 8.5s4.5-5.5 4.5-8.5a4.5 4.5 0 0 0-4.5-4.5z" fill="#fff"/><circle cx="4.5" cy="4.5" r="1.6" fill="#333"/></svg>
    <p class="abs foot-text" style="left:314px;top:1106px;width:90px">Lorem ipsum dolor sit amet, consectetuer adipiscing eli sed di nonmmy</p>
    <svg class="abs" style="left:428px;top:1108px" width="7" height="11" viewBox="0 0 7 11"><rect x=".5" y=".5" width="6" height="10" rx="1" fill="none" stroke="#fff"/><rect x="1.5" y="2" width="4" height="5" fill="#fff"/></svg>
    <p class="abs foot-text" style="left:445px;top:1106px;font-size:10.5px">123-456-7890</p>
    <svg class="abs" style="left:427px;top:1132px" width="11" height="8" viewBox="0 0 11 8"><rect width="11" height="8" fill="#fff"/><path d="M0 0l5.5 4.5 5.5-4.5" fill="none" stroke="#333"/></svg>
    <p class="abs foot-text" style="left:445px;top:1130px">info@verdalelodge37.com</p>
    <div class="abs" style="left:573px;top:1103px;height:52px;border-left:1px solid #555"></div>
    <div class="abs foot-brand"><i></i>VERDALE LODGE 37</div>
    <div class="abs footer-line" style="left:296px;top:1163px;width:398px"></div>
    <p class="abs foot-text" style="left:305px;top:1175px">© 2014 Verdale Lodge 37 &nbsp;| &nbsp;All Rights Reserved</p>
  </footer>

</div>
</body>
</html>
```